Distribution/Printing company needs a web site to inform prospective customers on what we do.

Distribution/Printing/Packaging company needs a web site to inform prospective customers on what we do. Please look at our direct to consumer web site (under development) for an idea of the product lines we sell: storedev.maplewickhaven.com
Logo files are attached as is a flyer that is under development which contains other information about the company (this is to be used for content- not to be posted as is). The web site should be focused on our business customer base and is not intended to be direct to consumer. Site should have a link to our consumer web site.
Site design should be mobile friendly, or mobile could be redirected to a mobile version. This web site will be strictly informational and will not be designed for any sales transactions.

Target Market(s)

Manufacturing and retail businesses, any other multi-site business that would benefit from centralized pricing and budget controls we can provide (banks, medical/dental offices, educational facilities, etc).

Industry/Entity Type

It Company

Coding

Coded - Design and coding required

Number of Pages Required

5+ page

Requirements
Must have
• 1) Top level menu: Products, about us, locations, contact us, news
• 2) page with news/promotions that is easily updated
• 3) "contact us" form (name, company, phone, email address) email link
• 4) link to www.store.maplewickhaven.com with information that lower pricing is available for businesses
• 5) SEO keywords
• 6) Link to powerpoint presentation file
Nice to have
• 1) our phone number should appear on every page near the top

```html
<!DOCTYPE html>
<html lang="en">
<head>
<meta charset="utf-8">
<title>Maplewick Haven Supply – Packaging, Printing, Distribution</title>
<link href="https://fonts.googleapis.com/css2?family=Ubuntu:wght@400;500;700&family=PT+Sans:wght@400;700&display=swap" rel="stylesheet">
<style>
:root{
  --page-bg:#e3e4e6;
  --page-bg-light:#f1f1f2;
  --navy:#0b3d68;
  --navy-dark:#062c4f;
  --navy-light:#1d5f8f;
  --text:#2b2b2b;
  --white:#ffffff;
  --footer:#232323;
  --band:#c9cacc;
  --button:#e9eaeb;
}
*{box-sizing:border-box;margin:0;padding:0}
html,body{width:1200px;height:1140px;overflow:hidden}
body{
  position:relative;
  font-family:"PT Sans",Arial,sans-serif;
  color:var(--text);
  background:linear-gradient(180deg,var(--page-bg-light) 0,var(--page-bg) 120px,#d3d4d6 190px,var(--page-bg) 560px,var(--page-bg-light) 760px);
}
.brand{position:absolute;left:179px;top:58px;width:280px;text-align:center;white-space:nowrap}
.brand-mark{display:block;width:14px;height:14px;background:#2a2a2a;margin:0 auto 10px}
.brand-name{font-family:"Ubuntu",sans-serif;font-weight:500;font-size:18px;line-height:22px;color:#2a2a2a;letter-spacing:.2px}
.brand-tagline{font-family:"Ubuntu",sans-serif;font-weight:500;font-size:13px;line-height:16px;color:#2a2a2a;margin-top:3px}
.language{position:absolute;left:732px;top:88px;display:flex;align-items:center;gap:8px;font-size:12px;color:#222}
.language-select{position:relative;width:133px;height:20px;background:var(--white);border:1px solid #c5c6c8;font-size:11.5px;line-height:18px;padding-left:6px}
.language-select span.toggle{position:absolute;right:-1px;top:-1px;width:22px;height:20px;background:var(--navy);display:flex;align-items:center;justify-content:center}
.hero{position:absolute;left:0;top:192px;width:1200px;height:346px;
  background:linear-gradient(180deg,#5e5aa8 0,#8a76b8 30%,#c79aa8 55%,#3b2a3a 75%,#121014 100%)}
.hero-arrow{position:absolute;top:138px;width:26px;height:44px}
.hero-arrow.prev{left:203px}.hero-arrow.next{left:970px}
.main-nav{position:absolute;left:203px;top:159px;width:794px;height:63px;border-radius:8px;
  background:linear-gradient(180deg,#1a5b8b 0,var(--navy) 50%,var(--navy-dark) 100%);
  box-shadow:0 2px 4px rgba(0,0,0,.3);display:flex;align-items:center;justify-content:center;gap:36px}
.main-nav a{font-family:"Ubuntu",sans-serif;font-size:16.5px;color:var(--white);text-decoration:none}
.nav-dot{width:13px;height:13px;border-radius:50%;border:3px solid var(--white)}
.services{position:absolute;top:474px;left:203px;width:794px;height:260px}
.service{position:absolute;top:0;width:241px}
.service:nth-child(1){left:0}.service:nth-child(2){left:278px}.service:nth-child(3){left:553px}
.service-image{height:123px;border:2px solid #2a6aa5;box-shadow:0 2px 6px rgba(0,0,0,.25)}
.service-title{margin-top:10px;height:31px;background:linear-gradient(180deg,#1d5f8f,var(--navy-dark));
  color:var(--white);font-family:"Ubuntu",sans-serif;font-weight:400;font-size:16.5px;line-height:31px;padding-left:10px}
.service p{margin-top:8px;font-size:11.3px;line-height:13.6px;text-align:justify;color:#2b2b2b}
.info-band{position:absolute;left:0;top:760px;width:1200px;height:240px;
  background:linear-gradient(180deg,#06365f 0,#0d4675 55%,#175683 100%)}
.info-band h2{position:absolute;top:26px;font-family:"PT Sans",sans-serif;font-weight:700;font-size:24px;line-height:30px;color:var(--white)}
.social{position:absolute;left:205px;top:86px;display:flex;gap:15px}
.social-link{width:46px;height:46px;border-radius:50%;background:radial-gradient(circle at 40% 35%,#9fc7ee,#3a7fc2 60%,#1d4f86);border:2px solid #dfe9f3}
.social-link.alt{background:radial-gradient(circle at 40% 35%,#f0a79b,#c94a3a 60%,#8f2a20)}
.blog-list{position:absolute;left:452px;top:62px;width:242px;list-style:none}
.blog-list li{position:relative;padding-left:20px;font-size:11.3px;line-height:13.6px;color:var(--white);text-align:justify;margin-bottom:14px}
.blog-list li::before{content:"";position:absolute;left:0;top:2px;width:10px;height:10px;border-radius:50%;border:2px solid var(--white)}
.btn{position:absolute;top:196px;height:24px;border-radius:5px;background:linear-gradient(180deg,#fff,#d3d4d6);
  font-family:"Ubuntu",sans-serif;font-weight:500;font-size:12.5px;color:#333;line-height:24px;text-align:center;text-decoration:none;box-shadow:0 1px 2px rgba(0,0,0,.4)}
.btn.more{left:471px;width:84px}.btn.send{left:912px;width:85px}
.contact-box{position:absolute;left:755px;top:61px;width:242px;height:126px;background:var(--white);border:3px solid #c9d2dc;
  box-shadow:inset 0 0 12px rgba(0,0,0,.25);padding:5px 7px;font-size:11.3px;line-height:13.6px;text-align:justify;color:#333}
.gray-band{position:absolute;left:0;top:1000px;width:1200px;height:27px;background:linear-gradient(180deg,#d8d9db,#c4c5c7)}
.site-footer{position:absolute;left:0;top:1027px;width:1200px;height:113px;background:var(--footer)}
.copyright{position:absolute;left:204px;top:40px;font-family:Arial,sans-serif;font-size:11px;color:var(--white)}
.footer-brand{position:absolute;left:758px;top:60px;width:240px;text-align:center;white-space:nowrap;color:var(--white);font-family:"Ubuntu",sans-serif;font-weight:500}
.footer-brand .name{font-size:14.5px;line-height:18px}.footer-brand .tag{font-size:10.5px;line-height:13px;margin-top:3px}
</style>
</head>
<body>
<header>
  <div class="brand">
    <span class="brand-mark"></span>
    <div class="brand-name">MAPLEWICK HAVEN SUPPLY</div>
    <div class="brand-tagline">Packaging • Printing • Distribution</div>
  </div>
  <div class="language">
    <span>Choose Your language:</span>
    <div class="language-select">English
      <span class="toggle"><svg width="10" height="8" viewBox="0 0 10 8"><path d="M0 0h10L5 8z" fill="#fff"/></svg></span>
    </div>
  </div>
</header>

<section class="hero" role="img" aria-label="Photograph of a city riverside skyline with a clock tower and parliament building at dusk">
  <svg class="hero-arrow prev" viewBox="0 0 26 44"><path d="M22 4L5 22l17 18" fill="none" stroke="#fff" stroke-width="6"/></svg>
  <svg class="hero-arrow next" viewBox="0 0 26 44"><path d="M4 4l17 18L4 40" fill="none" stroke="#fff" stroke-width="6"/></svg>
</section>

<nav class="main-nav">
  <a href="#">HOME</a><span class="nav-dot"></span>
  <a href="#">OFFER</a><span class="nav-dot"></span>
  <a href="#">ABOUT US</a><span class="nav-dot"></span>
  <a href="#">EXPERIENCE</a><span class="nav-dot"></span>
  <a href="#">CONTACT</a>
</nav>

<main class="services">
  <article class="service">
    <div class="service-image" role="img" aria-label="Photograph of folded cardboard packaging pieces" style="background:linear-gradient(135deg,#f2f2f0,#d9c2a2 60%,#eeeeec)"></div>
    <h3 class="service-title">Packaging</h3>
    <p>It is a long established fact that a reader will be distracted by the readable content of a page when looking at its layout. The point of using Lorem Ipsum is that it has a more-or-less normal distribution of letters, as opposed to using 'Content here, content here', making it look like readable English.</p>
  </article>
  <article class="service">
    <div class="service-image" role="img" aria-label="Photograph of a hand holding printed sheets" style="background:linear-gradient(120deg,#efefef,#dcdcdc 45%,#6b3a2a 75%,#2b2b33)"></div>
    <h3 class="service-title">Printing</h3>
    <p>It is a long established fact that a reader will be distracted by the readable content of a page when looking at its layout. The point of using Lorem Ipsum is that it has a more-or-less normal distribution of letters, as opposed to using 'Content here, content here', making it look like readable English.</p>
  </article>
  <article class="service">
    <div class="service-image" role="img" aria-label="Photograph of printed posters displayed at a street bus shelter" style="background:linear-gradient(90deg,#2aa7c9,#4fc0d8 45%,#e27a3a 60%,#3a4a55)"></div>
    <h3 class="service-title">Distribution</h3>
    <p>It is a long established fact that a reader will be distracted by the readable content of a page when looking at its layout. The point of using Lorem Ipsum is that it has a more-or-less normal distribution of letters, as opposed to using 'Content here, content here', making it look like readable English.</p>
  </article>
</main>

<section class="info-band">
  <h2 style="left:204px">Follow us</h2>
  <div class="social">
    <a class="social-link" href="#" aria-label="Social network link"></a>
    <a class="social-link" href="#" aria-label="Social network link"></a>
    <a class="social-link alt" href="#" aria-label="Social network link"></a>
  </div>
  <h2 style="left:452px">Blogs</h2>
  <ul class="blog-list">
    <li>Lorem Ipsum has been the industry's standard dummy text ever since the 1500s, when an unknown printer took a galley of type and scrambled it to make a type specimen book.</li>
    <li>Lorem Ipsum has been the industry's standard dummy text ever since the 1500s, when an unknown printer took a galley of type and scrambled it to make a type specimen book.</li>
  </ul>
  <a class="btn more" href="#">SEE MORE</a>
  <h2 style="left:755px">Contact us</h2>
  <div class="contact-box">Lorem Ipsum has been the industry's standard dummy text ever since the 1500s, when an unknown printer took a galley of type and scrambled it to make a type specimen book.</div>
  <a class="btn send" href="#">SEND</a>
</section>

<div class="gray-band"></div>
<footer class="site-footer">
  <p class="copyright">All Right Reserved 2015. Maplewick Haven supply.</p>
  <div class="footer-brand">
    <div class="name">MAPLEWICK HAVEN SUPPLY</div>
    <div class="tag">Packaging • Printing • Distribution</div>
  </div>
</footer>
</body>
</html>
```